Harbor Seal Works Spray Foam Appications website

We need a custom website for our company, www.harborsealworks.example. We need something we can modify by adding/changing content, photos, updated projects, etc. We are a commercial contractor specializing in Spray Foam applications. We want the website to be very creative and easy to navigate. The main points of the website are to showcase our projects, and describe our scope of services. We provide spray foam applications to the residential and commercial market. We offer Spray Foam roofing applications, as well as Spray Foam interior insulation applications. We also provide Roof Restoration Coating Systems to refurbish old and failing metal roofs. We would be ok with a one page web design if we can get the scope of our services to flow in a single page. The designer can decide if single or multiple pages works best for our business. One of the suppliers we work with is www.verdansupply.example.

Target Market(s)

Residential Home Builders, General Contractors, Commercial Construction Companies, Property Management Groups.

Industry/Entity Type

Insulation

Number of Pages Required

5+ page

Font styles to use
Serif
Sans Serif

Colors

Designer to choose colors to be used in the design.

Requirements
Must have
• We already have a Wix page, so website must be a Wix theme design. Nice easy to navigate format. Color matched to our current logo theme. We already have brochures and would like for it to match what's already in the hands of some of our customers. Need to be able to manage content to update photos, projects, scope of service, etc., via Wix. Current hold/splash page is hosted at www.harborsealworks.example. We would also like to have this video posted on the home page: https://www.videohost.example/watch?v=QxT4pLm9ZrA&feature=share
Nice to have
• I have attached some splash videos, being able to incorporate these somehow without being overpowering would be nice.

```html
<!DOCTYPE html>
<html lang="en">
<head>
<meta charset="utf-8">
<title>Harbor Seal Works</title>
<link rel="stylesheet" href="https://fonts.googleapis.com/css2?family=Lato:wght@400;700&family=Ubuntu:wght@500;700&display=swap">
<style>
  :root {
    --accent: #f0a81c;
    --ink: #333333;
    --text: #4a4a4a;
    --white: #ffffff;
    --footer: #0d0d0d;
    --muted: #9a9a9a;
  }
  * { margin: 0; padding: 0; box-sizing: border-box; }
  html, body { width: 1200px; height: 3858px; overflow: hidden; background: var(--white); }
  body { position: relative; font-family: "Lato", sans-serif; color: var(--text); }
  .abs { position: absolute; }
  h1, h2, h3 { font-family: "Ubuntu", sans-serif; font-weight: 500; }

  /* header */
  .site-header { left: 0; top: 0; width: 1200px; height: 108px; background: var(--white); }
  .brand { left: 75px; top: 24px; display: flex; align-items: center; gap: 12px; }
  .brand-mark { width: 60px; height: 60px; border: 4px solid var(--accent); border-radius: 50%; }
  .brand-name { font-family: "Lato", sans-serif; font-weight: 700; font-size: 22px; color: var(--ink); letter-spacing: 0.5px; }
  .nav { top: 0; height: 108px; display: flex; align-items: center; font-size: 15px; color: #222; letter-spacing: 0.3px; }
  .nav a { color: inherit; text-decoration: none; position: absolute; transform: translateX(-50%); white-space: nowrap; }
  .nav .active { color: var(--accent); font-weight: 700; }
  .nav .active::before { content: ""; position: absolute; left: 50%; top: 50%; width: 64px; height: 64px; transform: translate(-50%, -50%); border: 3px solid var(--accent); border-radius: 50%; border-top-color: transparent; border-bottom-color: var(--accent); clip-path: polygon(0 0,100% 0,100% 30%,0 30%,0 70%,100% 70%,100% 100%,0 100%); }

  /* hero */
  .hero { left: 0; top: 108px; width: 1200px; height: 704px; background: linear-gradient(120deg, #7a7364 0%, #cfc7b0 40%, #b0a58a 70%, #5d5546 100%); }
  .hero-title { left: 0; width: 1200px; top: 410px; text-align: center; font-size: 72px; font-weight: 700; color: var(--white); }
  .dots { left: 0; width: 1200px; top: 764px; display: flex; justify-content: center; gap: 10px; }
  .dots span { width: 9px; height: 9px; border-radius: 50%; background: var(--white); }
  .dots span.on { background: var(--accent); }

  /* services */
  .section-title { left: 0; width: 1200px; text-align: center; font-size: 38px; color: var(--ink); }
  .service { top: 942px; width: 332px; }
  .service .photo { width: 330px; height: 282px; }
  .service h3 { color: var(--accent); font-family: "Lato", sans-serif; font-weight: 700; font-size: 24px; line-height: 28px; margin-top: 28px; }
  .ticks { list-style: none; margin-top: 12px; font-size: 14.5px; line-height: 26px; color: var(--text); }
  .ticks li { position: relative; padding-left: 33px; margin-bottom: 3px; }
  .ticks svg { position: absolute; left: 2px; top: 8px; width: 13px; height: 11px; }
  .btn { display: inline-block; background: var(--accent); color: var(--white); font-size: 15px; letter-spacing: 0.3px; text-align: center; width: 136px; height: 40px; line-height: 40px; text-decoration: none; }
  .service .btn { position: absolute; top: 538px; left: 0; }

  /* video */
  .video { left: 0; top: 1590px; width: 1200px; height: 438px; background: linear-gradient(180deg, #6f5f7a 0%, #8a7a6e 45%, #5a5650 75%, #4f6a3a 100%); }
  .play { left: 560px; top: 1769px; }

  /* split sections */
  .split-text { width: 520px; }
  .split-text h2 { font-size: 33px; color: var(--ink); }
  .split-text p { font-size: 15px; line-height: 30.5px; margin-top: 18px; }
  .split-text .btn { margin-top: 34px; }
  .who-photo { left: 600px; top: 2028px; width: 527px; height: 508px; background: linear-gradient(90deg, #5b4a36 0%, #e9e5dc 35%, #d8d3c6 60%, #6a5842 100%); }
  .spf-photo { left: 0; top: 2536px; width: 600px; height: 508px; background: linear-gradient(180deg, #6f87a8 0%, #b9b09a 25%, #c9c09a 45%, #bcb892 70%, #9e9f8a 100%); }

  /* roof band */
  .roof { left: 0; top: 3044px; width: 1200px; height: 452px; background: linear-gradient(180deg, #3f5f92 0%, #6d86ac 45%, #b5bcc6 65%, #cfd3d8 100%); }
  .roof-title { left: 0; width: 1200px; top: 3228px; text-align: center; font-size: 66px; font-weight: 700; color: var(--white); }

  /* footer */
  .footer { left: 0; top: 3496px; width: 1200px; height: 362px; background: var(--footer); }
  .sub-title { left: 0; width: 1200px; top: 3562px; text-align: center; font-size: 29px; color: var(--white); }
  .email { left: 253px; top: 3646px; width: 541px; height: 32px; border-bottom: 1px solid #777; color: var(--white); font-size: 15px; line-height: 24px; }
  .sub-btn { left: 811px; top: 3636px; width: 135px; height: 40px; line-height: 40px; font-size: 14px; }
  .copy { left: 0; width: 1200px; top: 3758px; text-align: center; font-size: 13.5px; color: var(--muted); }
  .social { left: 0; width: 1200px; top: 3798px; display: flex; justify-content: center; gap: 30px; }
  .social span { width: 22px; height: 22px; border-radius: 50%; background: #6d6d6d; }
</style>
</head>
<body>

<header class="abs site-header">
  <div class="abs brand"><span class="brand-mark"></span><span class="brand-name">Harbor Seal Works</span></div>
  <nav class="abs nav" style="left:0;width:1200px;">
    <a class="active" style="left:592px;">HOME</a>
    <a style="left:702px;">ABOUT US</a>
    <a style="left:824px;">SERVICES</a>
    <a style="left:945px;">PROJECTS</a>
    <a style="left:1078px;">CONTACT US</a>
  </nav>
</header>

<section class="abs hero" role="img" aria-label="Installer in protective suit spraying foam insulation in an attic"></section>
<h1 class="abs hero-title">Harbor Seal Works</h1>
<div class="abs dots"><span class="on"></span><span></span><span></span></div>

<h2 class="abs section-title" style="top:866px;">Our Services</h2>

<article class="abs service" style="left:75px;">
  <div class="photo" role="img" aria-label="Warehouse interior walls covered in spray foam insulation" style="background:linear-gradient(180deg,#6b655c 0%,#d9d3c3 35%,#c9c2b0 65%,#2b2b2b 100%);"></div>
  <h3>Interior Foam Insulation</h3>
  <ul class="ticks">
    <li><svg viewBox="0 0 13 11"><path d="M1 6l4 4 7-9" fill="none" stroke="#333" stroke-width="2.4"/></svg>Improve energy efficiency - up to 45% energy savings.</li>
    <li><svg viewBox="0 0 13 11"><path d="M1 6l4 4 7-9" fill="none" stroke="#333" stroke-width="2.4"/></svg>Maintain consistent temperatures.</li>
    <li><svg viewBox="0 0 13 11"><path d="M1 6l4 4 7-9" fill="none" stroke="#333" stroke-width="2.4"/></svg>Increase racking strength.</li>
    <li><svg viewBox="0 0 13 11"><path d="M1 6l4 4 7-9" fill="none" stroke="#333" stroke-width="2.4"/></svg>Firm adherence to framing members and substrates.</li>
  </ul>
  <a class="btn">READ MORE</a>
</article>

<article class="abs service" style="left:435px;">
  <div class="photo" role="img" aria-label="Industrial building with yellow spray foam applied across the roof" style="background:linear-gradient(180deg,#3d5a9a 0%,#b8ad92 40%,#d8c66a 70%,#c7b866 100%);"></div>
  <h3>Foam Roof Application</h3>
  <ul class="ticks">
    <li><svg viewBox="0 0 13 11"><path d="M1 6l4 4 7-9" fill="none" stroke="#333" stroke-width="2.4"/></svg>Lifetime maintainable system</li>
    <li><svg viewBox="0 0 13 11"><path d="M1 6l4 4 7-9" fill="none" stroke="#333" stroke-width="2.4"/></svg>Seamless self - adhering system</li>
    <li><svg viewBox="0 0 13 11"><path d="M1 6l4 4 7-9" fill="none" stroke="#333" stroke-width="2.4"/></svg>Weather durability</li>
    <li><svg viewBox="0 0 13 11"><path d="M1 6l4 4 7-9" fill="none" stroke="#333" stroke-width="2.4"/></svg>Energy conservation</li>
    <li><svg viewBox="0 0 13 11"><path d="M1 6l4 4 7-9" fill="none" stroke="#333" stroke-width="2.4"/></svg>Zero thermal bridging</li>
  </ul>
  <a class="btn">READ MORE</a>
</article>

<article class="abs service" style="left:796px;">
  <div class="photo" role="img" aria-label="Worker applying white coating to a ribbed metal roof" style="background:linear-gradient(160deg,#2a2e3a 0%,#c9d2e4 30%,#e6ecf6 65%,#b9c4d8 100%);"></div>
  <h3>Roof Restoration / Coating Systems</h3>
  <ul class="ticks">
    <li><svg viewBox="0 0 13 11"><path d="M1 6l4 4 7-9" fill="none" stroke="#333" stroke-width="2.4"/></svg>Repair without replacing - eliminates tear off.</li>
    <li><svg viewBox="0 0 13 11"><path d="M1 6l4 4 7-9" fill="none" stroke="#333" stroke-width="2.4"/></svg>Warranties Available</li>
    <li><svg viewBox="0 0 13 11"><path d="M1 6l4 4 7-9" fill="none" stroke="#333" stroke-width="2.4"/></svg>Preserve, protect , and prolong roof life</li>
    <li><svg viewBox="0 0 13 11"><path d="M1 6l4 4 7-9" fill="none" stroke="#333" stroke-width="2.4"/></svg>Energy savings.</li>
  </ul>
  <a class="btn">READ MORE</a>
</article>

<section class="abs video" role="img" aria-label="Video preview showing a single-storey stone house at dusk"></section>
<svg class="abs play" width="80" height="80" viewBox="0 0 80 80" aria-label="Play video">
  <circle cx="40" cy="40" r="40" fill="#ffffff"/>
  <path d="M31 23l26 17-26 17z" fill="#111111"/>
</svg>

<div class="abs split-text" style="left:75px;top:2105px;">
  <h2>Who We Are</h2>
  <p>Harbor Seal Works is a Spray Foam and Coating Applications Company with a combined experience of over 20 plus years.<br>We specialize in a diverse range of Spray Foam applications as well as Roof Restoration Coating Systems. Our experiences are that these products provide superior performance and longevity to help our customers reduce energy costs and increase the overall integrity of their assets.</p>
  <a class="btn">READ MORE</a>
</div>
<div class="abs who-photo" role="img" aria-label="Installer in protective suit spraying foam between wall studs"></div>

<div class="abs spf-photo" role="img" aria-label="Yellow spray foam roof on an industrial building"></div>
<div class="abs split-text" style="left:629px;top:2614px;">
  <h2>Spray Polyurethane Foam (SPF)</h2>
  <p>Spray foam is a durable, and versatile product suitable for industrial, commercial, agricultural, and residential applications. It boasts the industry's strongest performance in energy efficiency and energy savings. This advanced system can be applied to any shape and substrate. Spray foam works by sealing the building envelope to stop conditioned air from escaping and preventing unwanted outside air from entering the structure.</p>
  <a class="btn">READ MORE</a>
</div>

<section class="abs roof" role="img" aria-label="Restored white metal roof under a blue sky"></section>
<h2 class="abs roof-title">Roof Restorations</h2>

<footer class="abs footer"></footer>
<h2 class="abs sub-title">Subscribe for hot updates</h2>
<div class="abs email">Enter Email Address</div>
<a class="abs btn sub-btn">SUBSCRIBE</a>
<p class="abs copy">Copyright © 2020, Company Name. All Right reserved. Privacy /&nbsp; Disclaimer</p>
<div class="abs social" aria-label="Social links"><span></span><span></span><span></span><span></span></div>

</body>
</html>
```